Business Card Design for Marketing Firm

Looking for business card design for higher end marketing firm. Clean but impressionable/trendy. We are a marketing firm that represents manufacturers in the foodservice equipment and supply industry. Our customers are end users such has hotels, restaurants, country clubs, convention centers and casinos as well as distributors of restaurants supplies and equipment, and manufacturers of foodservice equipment and supplies.
Target Market(s)
Hotels, Restaurants, Supply & Equipment Distributors, Foodservice Manufacturers
Industry/Entity Type
Foodservice/Hospitality
Contact Information for Business Card
Name, Title, Contact Number, Email, Website, Social Media, Address
Requirements
Must have
- Clean & Simple but Serious and Impressionable

```html
<!DOCTYPE html>
<html lang="en">
<head>
<meta charset="utf-8">
<title>Meridian Hospitality Reps — Business Card</title>
<link href="https://fonts.googleapis.com/css2?family=Montserrat:wght@500;600;700&family=Open+Sans:wght@400&display=swap" rel="stylesheet">
<style>
  :root {
    --navy: #2a2a78;
    --white: #ffffff;
    --backdrop: #ecebe8;
    --shadow: rgba(20, 20, 50, 0.22);
  }
  * { margin: 0; padding: 0; box-sizing: border-box; }
  html, body {
    width: 1200px;
    height: 834px;
    overflow: hidden;
    background: var(--backdrop);
  }
  .canvas {
    position: relative;
    width: 1200px;
    height: 834px;
    display: flex;
    align-items: center;
    justify-content: center;
    gap: 48px;
  }
  .card {
    position: relative;
    width: 520px;
    height: 297px;
    overflow: hidden;
    box-shadow: 0 10px 26px var(--shadow);
  }
  .card--front { background: var(--white); }
  .card--back { background: var(--navy); }

  .wave { position: absolute; inset: 0; width: 100%; height: 100%; }

  .wordmark {
    font-family: 'Montserrat', sans-serif;
    font-weight: 600;
    text-transform: uppercase;
    letter-spacing: 0.06em;
    line-height: 1.2;
    text-align: right;
  }
  .card--front .wordmark {
    position: absolute;
    top: 58px;
    left: 110px;
    color: var(--navy);
    font-size: 16px;
  }
  .card--back .wordmark {
    position: absolute;
    top: 96px;
    left: 0;
    width: 100%;
    text-align: center;
    color: var(--white);
    font-size: 27px;
  }
  .wordmark__line { display: block; }

  .contact {
    position: absolute;
    right: 26px;
    top: 126px;
    text-align: right;
    color: var(--white);
    font-family: 'Open Sans', sans-serif;
  }
  .contact__name {
    font-family: 'Montserrat', sans-serif;
    font-weight: 700;
    font-size: 18px;
    line-height: 1.2;
    letter-spacing: 0.03em;
    text-transform: uppercase;
  }
  .contact__title {
    font-family: 'Montserrat', sans-serif;
    font-weight: 500;
    font-size: 12.5px;
    letter-spacing: 0.04em;
    margin-bottom: 10px;
  }
  .contact__address { font-size: 12px; line-height: 1.4; margin-bottom: 6px; }
  .contact__row {
    display: flex;
    justify-content: flex-end;
    align-items: center;
    gap: 8px;
    font-size: 12px;
    line-height: 1.5;
  }
  .contact__icon { width: 11px; height: 11px; fill: var(--white); }

  .social {
    position: absolute;
    left: 50%;
    top: 200px;
    transform: translateX(-50%);
    display: flex;
    gap: 6px;
  }
  .social__dot {
    width: 14px;
    height: 14px;
    border: 1.2px solid var(--white);
    border-radius: 50%;
  }
</style>
</head>
<body>
<main class="canvas">

  <section class="card card--front" aria-label="Business card front">
    <svg class="wave" viewBox="0 0 520 297" preserveAspectRatio="none" aria-hidden="true">
      <path d="M0,290 C90,200 180,165 270,160 C320,157 345,120 370,80 C410,30 470,8 520,0 L520,297 L0,297 Z" fill="var(--navy)"/>
      <path d="M0,297 C90,208 180,173 270,168 C323,165 350,128 376,88 C412,42 465,18 520,10" fill="none" stroke="var(--white)" stroke-width="1.3"/>
    </svg>

    <div class="wordmark">
      <span class="wordmark__line">Meridian Hospitality</span>
      <span class="wordmark__line">Reps</span>
    </div>

    <div class="contact">
      <p class="contact__name">Daniel Reyes</p>
      <p class="contact__title">Managing Director</p>
      <p class="contact__address">Your address, City<br>State, Zip 1234</p>
      <p class="contact__row">123 456 789
        <svg class="contact__icon" viewBox="0 0 24 24" aria-hidden="true"><path d="M6.6 10.8a15.1 15.1 0 0 0 6.6 6.6l2.2-2.2a1 1 0 0 1 1-.25 11.4 11.4 0 0 0 3.6.57 1 1 0 0 1 1 1V20a1 1 0 0 1-1 1A17 17 0 0 1 3 4a1 1 0 0 1 1-1h3.5a1 1 0 0 1 1 1c0 1.25.2 2.45.57 3.57a1 1 0 0 1-.25 1z"/></svg>
      </p>
      <p class="contact__row">info@yourgmail.com
        <svg class="contact__icon" viewBox="0 0 24 24" aria-hidden="true"><path d="M2 5h20v14H2z M2 5l10 8 10-8" fill="var(--white)" stroke="var(--navy)" stroke-width="1.5"/></svg>
      </p>
      <p class="contact__row">www.yourwebsite.com
        <svg class="contact__icon" viewBox="0 0 24 24" aria-hidden="true"><circle cx="12" cy="12" r="10"/><path d="M2 12h20M12 2c3 3 3 17 0 20M12 2c-3 3-3 17 0 20" fill="none" stroke="var(--navy)" stroke-width="1.5"/></svg>
      </p>
    </div>
  </section>

  <section class="card card--back" aria-label="Business card back">
    <div class="wordmark">
      <span class="wordmark__line">Meridian Hospitality</span>
      <span class="wordmark__line">Reps</span>
    </div>
    <div class="social" aria-label="Social media links">
      <span class="social__dot"></span>
      <span class="social__dot"></span>
      <span class="social__dot"></span>
      <span class="social__dot"></span>
      <span class="social__dot"></span>
    </div>
  </section>

</main>
</body>
</html>
```